Professional, modern and unique business card. We are looking to present a new look to our business cards however we don't want to divert too far away from original template. We want social media links and our 3 office addresses on the backside of the business cards. Please see attached business card templates for ideas.
Crestline Homes Color Code:
R: 7
G:63
B:86

Target Market(s)

Real Estate

Industry/Entity Type

Real Estate

Contact Information for Business Card

Follow the attached templates. In need of a more modern and unique touch but don't want to divert from the original theme or color.
Crestline Homes Color Code:
R: 7
G:63
B:86

Font styles to use
Serif

Requirements
Must have
• Crestline Homes logo, Crestline homes colors, social media links, 3 office addresses,
Nice to have
• information about Crestline Homes and QR codes. You can check out www.mycrestlinehomes.example

```html
<!DOCTYPE html>
<html lang="en">
<head>
<meta charset="utf-8">
<title>Crestline Homes — Business Card</title>
<link rel="stylesheet" href="https://fonts.googleapis.com/css2?family=Oswald:wght@500&family=Work+Sans:wght@400;500&display=swap">
<style>
  :root {
    --stage: #161616;
    --card: #232323;
    --card-edge: #2b2b2b;
    --accent: #1b7fc3;
    --ink: #f1f1f1;
    --logo: #cfe6f2;
  }
  * { box-sizing: border-box; margin: 0; padding: 0; }
  html, body {
    width: 1200px; height: 900px; overflow: hidden;
    background: var(--stage);
    font-family: "Work Sans", sans-serif;
    color: var(--ink);
  }
  .sheet {
    position: relative; width: 1200px; height: 900px;
    display: flex; flex-direction: column; align-items: center; justify-content: center; gap: 36px;
  }
  .card {
    position: relative; width: 700px; height: 400px; overflow: hidden;
    background: linear-gradient(135deg, var(--card-edge), var(--card));
    border-bottom: 6px solid var(--accent);
  }
  /* front */
  .brand {
    position: absolute; top: 80px; left: 0; right: 0;
    display: flex; align-items: center; justify-content: center; gap: 18px;
  }
  .brand-dot { width: 34px; height: 34px; border-radius: 50%; background: var(--logo); }
  .brand-name {
    font-family: "Work Sans", sans-serif; font-weight: 500;
    font-size: 52px; letter-spacing: 1px; color: var(--logo);
  }
  .offices {
    position: absolute; left: 40px; right: 40px; bottom: 50px;
    display: flex; justify-content: space-between; align-items: center;
  }
  .office { font-size: 17px; line-height: 1.35; letter-spacing: .5px; }
  .office-divider { width: 2px; height: 38px; background: var(--ink); }
  /* back */
  .agent {
    position: absolute; left: 40px; top: 148px; width: 270px;
  }
  .agent-name {
    font-family: "Oswald", sans-serif; font-weight: 500;
    font-size: 42px; line-height: 1; color: var(--accent); text-transform: uppercase;
    white-space: nowrap;
  }
  .agent-title { font-size: 16px; letter-spacing: .6px; margin-top: 8px; white-space: nowrap; }
  .back-divider {
    position: absolute; left: 330px; top: 140px; width: 2px; height: 104px; background: var(--accent);
  }
  .contacts {
    position: absolute; left: 352px; top: 138px; list-style: none;
  }
  .contacts li {
    display: flex; align-items: center; gap: 10px;
    font-size: 16px; letter-spacing: .3px; line-height: 27px; white-space: nowrap;
  }
  .contacts svg { width: 13px; height: 13px; flex: none; }
</style>
</head>
<body>
<main class="sheet">
  <section class="card card-front">
    <div class="brand">
      <span class="brand-dot"></span>
      <span class="brand-name">Crestline Homes</span>
    </div>
    <div class="offices">
      <p class="office">418 Harbor Ave<br>Bayview, NY 11990</p>
      <span class="office-divider"></span>
      <p class="office">72-10 Maple Row<br>Elm Park, NY 11921</p>
      <span class="office-divider"></span>
      <p class="office">905 Union Way<br>Westfield, NY 11934</p>
    </div>
  </section>

  <section class="card card-back">
    <div class="agent">
      <h1 class="agent-name">Daniel Brooks</h1>
      <p class="agent-title">Associate Real Estate Broker</p>
    </div>
    <span class="back-divider"></span>
    <ul class="contacts">
      <li>
        <svg viewBox="0 0 16 16"><path d="M4 1l3 3-2 2c1 2 3 4 5 5l2-2 3 3-2 2C7 14 2 9 2 3z" fill="var(--accent)"/></svg>
        555-014-2871
      </li>
      <li>
        <svg viewBox="0 0 16 16"><rect x="4" y="1" width="8" height="14" rx="1.5" fill="none" stroke="var(--accent)" stroke-width="1.6"/><circle cx="8" cy="12.5" r="1" fill="var(--accent)"/></svg>
        555-014-3360
      </li>
      <li>
        <svg viewBox="0 0 16 16"><rect x="1.5" y="3.5" width="13" height="9" fill="none" stroke="var(--accent)" stroke-width="1.5"/><path d="M1.5 3.5l6.5 5 6.5-5" fill="none" stroke="var(--accent)" stroke-width="1.5"/></svg>
        info@mycrestlinehomes.example
      </li>
      <li>
        <svg viewBox="0 0 16 16"><circle cx="8" cy="8" r="6.5" fill="none" stroke="var(--accent)" stroke-width="1.4"/><ellipse cx="8" cy="8" rx="2.8" ry="6.5" fill="none" stroke="var(--accent)" stroke-width="1.2"/><path d="M1.5 8h13" stroke="var(--accent)" stroke-width="1.2"/></svg>
        www.mycrestlinehomes.example
      </li>
    </ul>
  </section>
</main>
</body>
</html>
```